Photography business - business card design quick turn around

Create a business card design for me please. I actually need the final design back before the end of Sunday 13th May 7pm GMT. Sorry for the short notice.

Photoshop artwork template uploaded with artwork guidelines including printer profiles and other mandatory specifications. Only one side of the business card is required as the other side will be an image.

The design is required as an unflattened PSD file so that I can edit the text if I need to.

My brand colours are white and the teal you see in the logo. Occasionally I also use a dark grey on my website (I don't mind the shade of grey as appreciate grey on teal would be a different grey, to the grey I use on white on the website, so just use a shade of grey that matches). Font can be as the font for the logo or if you prefer I am open to another sans serif, easily legible font. Ideally font size will be 12+.Please do not use capital letters for text. I prefer everything to be lower case, if possible.

Thank you.

Lena

Target Market(s)

Other business owners who may refer me and families

Industry/Entity Type

Photographer

Contact Information for Business Card

Silver Kettle Photography Logo
Sub text: family portraiture, captured with love

Contact information, ideally using simple icons to represent email / website / facebook / instagram / pinterest

email: lena@silverkettlephotography.co.uk
website: silverkettlephotography.co.uk
facebook: @silverkettlephotography
pinterest: pinterest.com/silverkettlepho
instagram: @silverkettle_photography
mobile/telephone: 07713460291

If there is too much text then please drop the instagram and pinterest information.

Font styles to use
Sans Serif

Colors
33b8a4

Requirements
Must have
• Logo
• Contact details as listed above
• sub text
Nice to have
• Instagram and Pinterest contact details
• Nice to have icons to represent website / phone / facebook etc followered by the handle where relevant

```html
<!DOCTYPE html>
<html lang="en">
<head>
<meta charset="utf-8">
<title>Silver Kettle Photography – Business Card</title>
<link rel="stylesheet" href="https://fonts.googleapis.com/css2?family=Didact+Gothic&family=Montserrat:wght@600&display=swap">
<style>
  :root {
    --backdrop: #3a3a3c;
    --card-white: #ffffff;
    --teal: #06cfbf;
    --grey: #4b4b4d;
    --ink: #141414;
    --on-teal: #ffffff;
  }
  * { box-sizing: border-box; margin: 0; padding: 0; }
  html, body { width: 1200px; height: 1000px; overflow: hidden; }
  body {
    background: var(--backdrop);
    display: flex; align-items: center; justify-content: center;
  }
  .business-card {
    width: 900px; height: 520px;
    border-radius: 40px;
    overflow: hidden;
    background: var(--card-white);
    display: flex; flex-direction: column;
    box-shadow: 0 20px 40px rgba(0,0,0,.35);
  }
  .brand-area {
    height: 300px;
    display: flex; flex-direction: column; align-items: center; justify-content: center;
    gap: 14px;
  }
  .brand-lockup { display: flex; align-items: center; gap: 22px; }
  .brand-dot { width: 56px; height: 56px; border-radius: 50%; background: var(--ink); }
  .brand-name {
    font-family: "Didact Gothic", sans-serif;
    font-size: 54px; color: var(--ink); letter-spacing: 1px;
    text-transform: lowercase;
  }
  .tagline {
    font-family: "Didact Gothic", sans-serif;
    font-size: 24px; letter-spacing: 3px; color: var(--ink);
  }
  .divider-band { height: 8px; background: var(--grey); }
  .contact-band {
    flex: 1; background: var(--teal);
    display: flex; align-items: center; justify-content: center;
    gap: 36px;
    font-family: "Montserrat", sans-serif; font-weight: 600;
    font-size: 21px; color: var(--on-teal);
  }
  .contact-list, .social-list { list-style: none; display: flex; flex-direction: column; gap: 14px; }
  .contact-list li { display: flex; align-items: center; justify-content: flex-end; gap: 12px; }
  .social-list li { display: flex; align-items: center; gap: 12px; }
  .column-rule { width: 2px; align-self: stretch; margin: 36px 0; background: var(--grey); }
  .icon {
    width: 26px; height: 26px; border-radius: 50%; background: var(--grey);
    display: flex; align-items: center; justify-content: center; flex: none;
  }
  .icon svg { width: 16px; height: 16px; }
</style>
</head>
<body>
  <section class="business-card">
    <header class="brand-area">
      <div class="brand-lockup">
        <span class="brand-dot"></span>
        <span class="brand-name">silver kettle photography</span>
      </div>
      <p class="tagline">family portraiture, captured with love</p>
    </header>
    <div class="divider-band"></div>
    <footer class="contact-band">
      <ul class="contact-list">
        <li>07713460291
          <span class="icon"><svg viewBox="0 0 16 16"><path d="M4 2l2 3-1.5 1.5a8 8 0 0 0 5 5L11 10l3 2-1.5 2.5C7 14 2 9 1.5 3.5z" fill="#fff"/></svg></span>
        </li>
        <li>lena@silverkettlephotography.co.uk
          <span class="icon"><svg viewBox="0 0 16 16"><rect x="2" y="4" width="12" height="8" fill="none" stroke="#fff" stroke-width="1.5"/><path d="M2 4l6 5 6-5" fill="none" stroke="#fff" stroke-width="1.5"/></svg></span>
        </li>
        <li>silverkettlephotography.co.uk
          <span class="icon"><svg viewBox="0 0 16 16" fill="none" stroke="#fff" stroke-width="1.3"><circle cx="8" cy="8" r="6"/><ellipse cx="8" cy="8" rx="2.6" ry="6"/><path d="M2 8h12"/></svg></span>
        </li>
      </ul>
      <div class="column-rule"></div>
      <ul class="social-list">
        <li><span class="icon"></span>@silverkettlephotography</li>
        <li><span class="icon"></span>silverkettlepho</li>
        <li><span class="icon"></span>@silverkettle_photography</li>
      </ul>
    </footer>
  </section>
</body>
</html>
```